New Business Card for Web Design/Internet Marketing Company

Looking for a great looking new business card. We are a 10 year old web design, internet marketing and website management company that works mostly with small businesses.

Our new card needs to better match the colors and style of our website, be bold, extremely usable and slightly edgy.

Target Market(s)

Small/Medium businesses that have websites

Industry/Entity Type

Internet

Requirements
Must have
• Front and back design, full color, rounded corners please

Must use the colors/style of our website (JPG provided)

INFO FOR CARDS (as readable as possible please)
Mark Lenner
President/CEO
mark@trelvanmedia.example
Phone: 520-381-7459
Toll Free: 866-381-7459
Address: 4315 W. Calloway Ave. Ste. 140, Tucson, AZ 85792

THINGS I WANT TO PROMOTE (if there is room):
1. Our Website - www.trelvanmedia.example

2. Social Media
Twitter: @trelvanmedia
Facebook: www.facebook.com/trelvanmedia

3. Our Services
Web Design
Internet Marketing
Website Management

```html
<!DOCTYPE html>
<html lang="en">
<head>
<meta charset="utf-8">
<title>Trelvan Media – Business Card</title>
<link href="https://fonts.googleapis.com/css2?family=Lato:wght@400;700;900&display=swap" rel="stylesheet">
<style>
  :root {
    --canvas-bg: #e9e6e1;
    --card-white: #f4f4f3;
    --ink: #3d3d3d;
    --ink-soft: #555a60;
    --brand-blue: #1466b8;
    --band-light: #2f86d6;
    --band-dark: #0b3f86;
    --navy-deep: #050c3a;
    --navy-mid: #0a2a9a;
    --accent-orange: #e07a1b;
    --icon-blue: #3c8fc4;
  }
  * { box-sizing: border-box; margin: 0; padding: 0; }
  html, body { width: 1200px; height: 720px; overflow: hidden; }
  body {
    background: var(--canvas-bg);
    font-family: "Lato", sans-serif;
    position: relative;
  }
  .card {
    position: absolute;
    top: 212px;
    width: 520px;
    height: 297px;
    border-radius: 14px;
    overflow: hidden;
    box-shadow: 0 6px 18px rgba(0,0,0,0.18);
  }
  /* Front */
  .card-front { left: 50px; background: var(--card-white); color: var(--ink); }
  .brand-name {
    position: absolute;
    font-weight: 700;
    letter-spacing: 0.2px;
  }
  .card-front .brand-name {
    top: 30px; right: 30px;
    font-size: 22px;
    color: var(--brand-blue);
  }
  .person { position: absolute; left: 28px; top: 72px; }
  .person-name { font-size: 22px; font-weight: 400; }
  .person-title { font-size: 13px; color: var(--ink-soft); margin-top: 2px; }
  .contact-list { position: absolute; left: 28px; top: 128px; list-style: none; }
  .contact-list li {
    display: flex; align-items: center; gap: 9px;
    font-size: 13px; line-height: 17px; color: var(--ink);
  }
  .contact-list svg { width: 12px; height: 12px; flex: none; }
  .address { position: absolute; left: 28px; top: 194px; font-size: 13px; line-height: 17px; }
  .social-list { position: absolute; right: 30px; top: 108px; list-style: none; }
  .social-list li {
    display: flex; align-items: center; gap: 8px;
    font-size: 13px; line-height: 24px; color: var(--ink);
  }
  .social-mark { width: 14px; height: 14px; border-radius: 2px; background: var(--icon-blue); }
  .web-band {
    position: absolute; left: 0; right: 0; top: 234px; height: 38px;
    background: linear-gradient(180deg, var(--band-light), var(--band-dark));
    display: flex; align-items: center; justify-content: flex-end;
    padding-right: 36px;
  }
  .web-band span { color: #fff; font-weight: 700; font-size: 16px; letter-spacing: 0.3px; }
  /* Back */
  .card-back {
    left: 630px;
    background: radial-gradient(ellipse at 50% 35%, var(--navy-mid) 0%, #07197a 40%, var(--navy-deep) 100%);
  }
  .card-back .brand-name {
    left: 0; right: 0; top: 92px; text-align: center;
    font-size: 38px;
    color: var(--accent-orange);
  }
  .service-band {
    position: absolute; left: 0; right: 0; top: 186px; height: 36px;
    background: linear-gradient(180deg, var(--band-light), var(--band-dark));
    display: flex; align-items: center; justify-content: center;
  }
  .service-band span { color: #fff; font-size: 14px; padding: 0 16px; }
  .service-band span + span { border-left: 1px solid rgba(255,255,255,0.6); }
</style>
</head>
<body>

<section class="card card-front" aria-label="Card front">
  <div class="brand-name">Trelvan Media</div>

  <div class="person">
    <div class="person-name">Mark Lenner</div>
    <div class="person-title">President / CEO</div>
  </div>

  <ul class="contact-list">
    <li>
      <svg viewBox="0 0 12 12" aria-hidden="true"><rect x="1" y="1" width="10" height="10" rx="1.5" fill="none" stroke="var(--icon-blue)" stroke-width="1.4"/><rect x="3" y="3" width="6" height="2" fill="var(--icon-blue)"/><rect x="3" y="7" width="2" height="2" fill="var(--icon-blue)"/><rect x="7" y="7" width="2" height="2" fill="var(--icon-blue)"/></svg>
      520-381-7459
    </li>
    <li>
      <svg viewBox="0 0 12 12" aria-hidden="true"><rect x="3" y="0.5" width="6" height="11" rx="1.2" fill="none" stroke="var(--icon-blue)" stroke-width="1.4"/><rect x="4.3" y="2" width="3.4" height="5" fill="var(--icon-blue)"/></svg>
      866-381-7459 free
    </li>
    <li>
      <svg viewBox="0 0 12 12" aria-hidden="true"><rect x="0.7" y="2.5" width="10.6" height="7" fill="none" stroke="var(--icon-blue)" stroke-width="1.3"/><path d="M1 3l5 4 5-4" fill="none" stroke="var(--icon-blue)" stroke-width="1.3"/></svg>
      mark@trelvanmedia.example
    </li>
  </ul>

  <p class="address">4315 W. Calloway Ave. Ste. 140,<br>Tucson, AZ 85792</p>

  <ul class="social-list">
    <li><span class="social-mark"></span>@trelvanmedia</li>
    <li><span class="social-mark"></span>/trelvanmedia</li>
  </ul>

  <div class="web-band"><span>www.trelvanmedia.example</span></div>
</section>

<section class="card card-back" aria-label="Card back">
  <div class="brand-name">Trelvan Media</div>
  <div class="service-band">
    <span>Web Design</span>
    <span>Internet Marketing</span>
    <span>Website Management</span>
  </div>
</section>

</body>
</html>
```